Bramblewood Card Company Business Cards

We are a trading card store with Glimmorax, sports and other TCG cards, we need a business card design that encompasses a clean cut, modern style with a retro flare. website is bramblewoodcardco.com for reference. Can utilize a comic book era feel or a more modern outdoor feel to utilize the "Pacific Northwest" elements of tress, mountains, etc.

Industry/Entity Type

Trading cards and collectibles

Contact Information for Business Card

business name, email address, phone number, name, owner job title

Font styles to use
Sans Serif

```html
<!DOCTYPE html>
<html lang="en">
<head>
<meta charset="utf-8">
<title>Bramblewood Card Company – Business Cards</title>
<link rel="stylesheet" href="https://fonts.googleapis.com/css2?family=Montserrat:wght@300;400;800&display=swap">
<style>
  :root {
    --page: #2b2b2b;
    --card: #1f1f20;
    --cyan: #1fbde0;
    --grey: #7a7a7a;
    --rule: #5a5a5a;
    --white: #f4f4f4;
  }
  * { box-sizing: border-box; margin: 0; padding: 0; }
  html, body { width: 1200px; height: 900px; overflow: hidden; }
  body {
    background: var(--page);
    font-family: "Montserrat", Arial, sans-serif;
    color: var(--white);
    position: relative;
  }
  .card {
    position: absolute;
    left: 250px;
    width: 700px;
    height: 400px;
    background: var(--card);
    border-radius: 22px;
    overflow: hidden;
    box-shadow: 0 10px 30px rgba(0,0,0,.45);
  }
  .card--front { top: 30px; }
  .card--back { top: 470px; }

  .brand {
    display: flex;
    align-items: center;
    gap: 14px;
    font-weight: 800;
    text-transform: uppercase;
    color: var(--white);
    letter-spacing: .04em;
    line-height: 1.1;
  }
  .brand__dot {
    flex: none;
    border-radius: 50%;
    background: var(--cyan);
  }
  .card--front .brand {
    position: absolute;
    left: 50%; top: 50%;
    transform: translate(-50%, -50%);
    font-size: 30px;
    width: 440px;
  }
  .card--front .brand__dot { width: 44px; height: 44px; }

  .card--back .brand {
    position: absolute;
    right: 44px; top: 44px;
    font-size: 20px;
    width: 270px;
  }
  .card--back .brand__dot { width: 30px; height: 30px; }

  .person {
    position: absolute;
    left: 44px; top: 118px;
  }
  .person__name {
    font-weight: 800;
    font-size: 30px;
    color: var(--cyan);
    letter-spacing: .04em;
    text-transform: uppercase;
    line-height: 1;
  }
  .person__title {
    font-weight: 400;
    font-size: 18px;
    line-height: 1.2;
    margin-top: 8px;
  }
  .divider {
    position: absolute;
    left: 40px; right: 40px; top: 196px;
    height: 1px;
    background: var(--rule);
  }
  .contacts {
    position: absolute;
    left: 44px; top: 220px;
    list-style: none;
    font-weight: 400;
    font-size: 19px;
  }
  .contacts li {
    display: flex;
    align-items: center;
    gap: 14px;
    margin-bottom: 10px;
  }
  .contacts svg { width: 18px; height: 18px; flex: none; }
  .contacts .accent { color: var(--cyan); }
  .address {
    position: absolute;
    right: 44px; top: 222px;
    text-align: right;
    font-weight: 400;
    font-size: 17px;
    line-height: 1.45;
  }
  .foot-band {
    position: absolute;
    left: 0; bottom: 0;
    width: 100%; height: 22px;
  }
</style>
</head>
<body>

  <section class="card card--front" aria-label="Card front">
    <div class="brand"><span class="brand__dot"></span><span>Bramblewood Card Company</span></div>
  </section>

  <section class="card card--back" aria-label="Card back">
    <div class="brand"><span class="brand__dot"></span><span>Bramblewood Card Company</span></div>

    <div class="person">
      <p class="person__name">Dorian Vale</p>
      <p class="person__title">CEO/Founder</p>
    </div>

    <div class="divider"></div>

    <ul class="contacts">
      <li>
        <svg viewBox="0 0 24 24" aria-hidden="true"><path fill="#1fbde0" d="M6.6 10.8a15 15 0 0 0 6.6 6.6l2.2-2.2c.3-.3.7-.4 1-.2 1.1.4 2.3.6 3.6.6.6 0 1 .4 1 1V20c0 .6-.4 1-1 1A17 17 0 0 1 3 4c0-.6.4-1 1-1h3.5c.6 0 1 .4 1 1 0 1.3.2 2.5.6 3.6.1.3 0 .7-.2 1z"/></svg>
        <span>(555) 014 2290</span>
      </li>
      <li>
        <svg viewBox="0 0 24 24" aria-hidden="true"><path fill="#1fbde0" d="M2 5h20v14H2z M2 5l10 8 10-8" stroke="#1f1f20" stroke-width="1.5"/></svg>
        <span>info@bramblewoodcardco.com</span>
      </li>
      <li>
        <svg viewBox="0 0 24 24" aria-hidden="true"><g fill="none" stroke="#1fbde0" stroke-width="2"><circle cx="12" cy="12" r="9"/><path d="M3 12h18M12 3c3 3 3 15 0 18M12 3c-3 3-3 15 0 18"/></g></svg>
        <span>www.<span class="accent">bramblewoodcardco</span>.com</span>
      </li>
    </ul>

    <p class="address">P.O. Box 7731 Fernhill Road<br>Larchmont WA 98190</p>

    <svg class="foot-band" viewBox="0 0 700 22" preserveAspectRatio="none" aria-hidden="true">
      <polygon points="0,22 0,8 460,8 440,22" fill="#1fbde0"/>
      <polygon points="440,22 460,8 472,0 700,0 700,22" fill="#7a7a7a"/>
    </svg>
  </section>

</body>
</html>
```